A website for a Maltese Law Firm

Our law firm needs a website to further its business. The site should have a simple yet effective design. We would need the following sections: About us, Practice Areas, About Malta, Contact. These should be further split as follows:

About us: Our firm, Our values, What others say, Offices

Practice Areas: Crimimal, Citizenship & Residence, Sovereign Patron Pathway, Criminal Defence, Civil Litigation, Arbitration and ADR, Commercial and Corporate, Media Law.

About Malta: just one section.

Contact: Just one section

We would also need a news feed at the front of the site to include latest news regarding our cases.

At the bottom we need a section for our Terms and a Privacy Statement.

Our logo is being attached.

Target Market(s)

All clients looking for legal assistance in Malta

Industry/Entity Type

Legal

Coding

Coded - Design and coding required

Number of Pages Required

1 page

Requirements
Must have
• It must be simple yet striking.

```html
<!DOCTYPE html>
<html lang="en">
<head>
<meta charset="utf-8">
<title>Galea &amp; Spiteri Advocates</title>
<link href="https://fonts.googleapis.com/css2?family=Cinzel:wght@400;700&family=Lato:wght@400;700&family=Raleway:wght@400;500;700&display=swap" rel="stylesheet">
<style>
:root{
  --ink:#111;
  --topbar:#0d0d0d;
  --nav:#1b1b1b;
  --paper:#f4f4f4;
  --white:#fff;
  --text:#555;
  --accent:#2f8fd0;
  --footer:#1d1d1d;
  --copy:#d2d2d2;
  --serif:'Cinzel', serif;
  --sans:'Raleway', sans-serif;
  --body:'Lato', sans-serif;
}
*{margin:0;padding:0;box-sizing:border-box}
html,body{width:1200px;height:3727px;overflow:hidden}
body{position:relative;background:var(--white);font-family:var(--sans);color:var(--text)}
.abs{position:absolute}

/* top bar */
.topbar{left:0;top:0;width:1200px;height:30px;background:var(--topbar);color:#ccc;font-family:var(--body);font-size:14px}
.topbar .social{position:absolute;left:88px;top:7px;display:flex;gap:14px}
.topbar .social span{width:14px;height:14px;border:1px solid #999;border-radius:2px;display:block}
.topbar .phone{position:absolute;right:82px;top:6px;display:flex;align-items:center;gap:10px}

/* header */
.header{left:0;top:30px;width:1200px;height:82px;background:var(--nav)}
.wordmark{font-family:var(--serif);font-weight:400;color:var(--white);letter-spacing:1px;line-height:1;white-space:nowrap}
.header .wordmark{position:absolute;left:104px;top:27px;font-size:28px}
.nav{position:absolute;right:82px;top:32px;display:flex;gap:34px;font-family:var(--serif);font-size:15px;color:#ddd}
.nav .active{color:var(--white);border-bottom:2px solid var(--white);padding-bottom:4px}

/* hero */
.hero{left:0;top:112px;width:1200px;height:571px;background:linear-gradient(180deg,#4f79b5 0%,#8fb3d8 32%,#c9a07a 52%,#e08a3b 60%,#335f96 72%,#1f4f86 100%)}
.hero-arrow{position:absolute;top:300px;width:30px;height:40px;background:rgba(0,0,0,.55);display:flex;align-items:center;justify-content:center}
.hero h1{position:absolute;left:104px;top:440px;font-family:var(--serif);font-weight:400;font-size:38px;line-height:50px;color:var(--white);letter-spacing:1px}

/* about */
.about{left:0;top:683px;width:1200px;height:510px;background:var(--paper);text-align:center}
.section-title{font-family:var(--serif);font-size:40px;color:var(--ink);font-weight:400;letter-spacing:1px}
.section-title u{text-decoration:none;border-bottom:2px solid #333;padding-bottom:2px}
.about .section-title{position:absolute;left:0;width:1200px;top:42px}
.about .copy{position:absolute;left:100px;width:1000px;top:150px;font-size:15px;line-height:24px;color:#666}
.about .copy p+p{margin-top:24px}
.feature{position:absolute;top:360px;display:flex;gap:20px;text-align:left}
.feature .icon{width:98px;height:98px;border:1px solid #ccc;background:var(--white);display:flex;align-items:center;justify-content:center}
.feature h3{font-family:var(--serif);font-weight:400;font-size:17px;color:var(--ink);margin-top:2px}
.feature p{font-size:13px;line-height:19px;color:#777;width:250px;margin-top:8px}

/* practice */
.practice{left:0;top:1193px;width:1200px;height:1329px;background:var(--white)}
.practice .section-title{position:absolute;left:0;width:1200px;top:36px;text-align:center}
.tile{position:absolute;width:328px;height:355px;overflow:hidden}
.tile .photo{position:absolute;inset:0}
.tile .shade{position:absolute;left:0;right:0;bottom:0;height:60%;background:linear-gradient(180deg,rgba(61,147,199,0),rgba(61,147,199,.9))}
.tile .label{position:absolute;left:0;right:0;bottom:18px;text-align:center;font-family:var(--serif);font-size:25px;line-height:28px;color:var(--white);letter-spacing:1px}
.tile.hover .shade{height:100%;background:rgba(61,147,199,.72)}
.tile.hover .label{bottom:auto;top:140px}
.tile.hover .blurb{position:absolute;left:40px;right:40px;top:180px;text-align:center;font-size:14px;font-weight:700;line-height:20px;color:var(--white)}
.tile.hover .plus{position:absolute;left:145px;top:278px}

/* case studies */
.cases{left:0;top:2522px;width:1200px;height:530px;background:radial-gradient(ellipse at 50% 40%,#3a2d24 0%,#1a1512 65%,#0f0c0a 100%)}
.cases .section-title{position:absolute;left:0;width:1200px;top:40px;text-align:center;color:var(--white)}
.cases .section-title u{border-color:#ddd}
.case{position:absolute;top:140px;width:330px}
.case .frame{width:330px;height:160px;border:6px solid #777;position:relative}
.case .frame .photo{position:absolute;inset:0}
.case .date{position:absolute;left:8px;top:8px;width:44px;text-align:center;font-family:var(--body);font-size:14px;font-weight:700}
.case .date .d{background:#222;color:var(--white);display:block;line-height:20px}
.case .date .m{background:var(--white);color:#333;display:block;line-height:20px}
.case h4{font-family:var(--body);font-size:14px;color:var(--accent);margin-top:22px;font-weight:700}
.case p{font-family:var(--body);font-size:13px;line-height:19px;color:#ddd;margin-top:8px}
.case .more{font-family:var(--body);font-size:13px;color:var(--accent);margin-top:14px;display:block}
.view-all{position:absolute;left:538px;top:2995px;display:flex;height:34px}
.view-all span{background:#ddd;color:#333;font-family:var(--body);font-size:12px;line-height:34px;padding:0 20px}
.view-all b{width:36px;background:#333;display:flex;align-items:center;justify-content:center}

/* testimonials */
.testimonials{left:0;top:3052px;width:1200px;height:360px;background:var(--white)}
.testimonials .section-title{position:absolute;left:0;width:1200px;top:52px;text-align:center}
.t-arrow{position:absolute;top:180px;width:34px;height:34px;border-radius:50%;display:flex;align-items:center;justify-content:center}
.quote{position:absolute;top:148px;display:flex;gap:26px}
.quote .who{width:100px;text-align:center}
.quote .avatar{width:96px;height:96px;border-radius:50%;border:4px solid #ddd;background:linear-gradient(180deg,#b9c3cc,#6f7c88)}
.quote .name{font-family:var(--body);font-size:13px;font-weight:700;color:#333;margin-top:16px}
.quote p{font-size:13px;line-height:20px;color:#777;width:420px;margin-top:6px}
.divider{position:absolute;left:600px;top:3200px;width:1px;height:150px;background:#ddd}

/* footer */
.footer{left:0;top:3412px;width:1200px;height:271px;background:var(--footer);color:#ddd;font-family:var(--body);font-size:12px}
.footer h5{font-family:var(--sans);font-weight:500;font-size:15px;color:var(--accent);letter-spacing:1px;border-bottom:1px solid #444;padding-bottom:8px;margin-bottom:14px}
.links{position:absolute;left:82px;top:40px;width:150px}
.links li{list-style:none;line-height:28px;padding-left:14px;position:relative}
.links li::before{content:"";position:absolute;left:2px;top:12px;width:4px;height:4px;background:#ccc;border-radius:50%}
.contact{position:absolute;left:300px;top:40px;width:200px}
.contact .row{display:flex;gap:10px;align-items:flex-start;line-height:17px;margin-bottom:12px}
.map{position:absolute;left:527px;top:92px;width:243px;height:117px;border:3px solid #ccc;background:linear-gradient(135deg,#e9e4d8,#d3dbe2)}
.footer .wordmark{position:absolute;left:862px;top:14px;width:244px;text-align:center;font-size:22px}
.f-social{position:absolute;left:910px;top:56px;display:flex;gap:14px}
.f-social span{width:34px;height:34px;border-radius:50%;background:#3b6fb6;border:2px solid #fff}
.f-social span:nth-child(4){background:#d44a3a}
.legal{position:absolute;left:900px;top:176px;color:#666;font-size:12px;display:flex;gap:26px}
.copyright{left:0;top:3683px;width:1200px;height:44px;background:var(--copy);font-family:var(--body);font-size:12px;color:#444;line-height:44px;padding-left:92px}
</style>
</head>
<body>

<div class="abs topbar">
  <div class="social"><span></span><span></span><span></span><span></span></div>
  <div class="phone">
    <svg width="12" height="18" viewBox="0 0 12 18"><rect x="1" y="1" width="10" height="16" rx="2" fill="none" stroke="#ccc" stroke-width="1.5"/><circle cx="6" cy="14" r="1" fill="#ccc"/></svg>
    555-014-2290
  </div>
</div>

<header class="abs header">
  <div class="wordmark">Galea &amp; Spiteri</div>
  <nav class="nav"><span class="active">Home</span><span>About Us</span><span>Practice Areas</span><span>Case Studies</span><span>Contact Us</span></nav>
</header>

<section class="abs hero" role="img" aria-label="Evening view of a harbour city skyline with a domed church lit over the water">
  <div class="hero-arrow" style="left:10px"><svg width="10" height="16"><path d="M8 2 L2 8 L8 14" stroke="#fff" stroke-width="2" fill="none"/></svg></div>
  <div class="hero-arrow" style="right:10px"><svg width="10" height="16"><path d="M2 2 L8 8 L2 14" stroke="#fff" stroke-width="2" fill="none"/></svg></div>
  <h1>Realize Your Constitutional<br>Right For Qualified Legal Help</h1>
</section>

<section class="abs about">
  <h2 class="section-title">About <u>Galea &amp; Spiteri</u></h2>
  <div class="copy">
    <p>Lorem ipsum dolor sit amet, consectetuer adipiscing elit, sed diam nonummy nibh euismod tincidunt ut laoreet dolore magna aliquam erat volutpat. Ut wisi enim ad minim veniam, quis nostrud exerci tation ullamcorper suscipit lobortis nisl ut aliquip ex eam commodo consequat. Duis autem vel eum iriure dolor in hendrerit in vulputate velit molestie consequat nulla facilisi.</p>
    <p>Lorem ipsum dolor sit amet, consectetuer adipiscing elit, sed diam nonummy nibh euismod tincidunt ut laoreet dolore magna aliquam erat volutpat. Ut wisi enim ad minim veniam, quis nostrud exerci tation ullamcorper suscipit lobortis nisl ut aliquip ex eam commodo consequat. Duis autem vel eum iriure dolor in hendrerit in vulputate velit molestie consequat nulla facilisi.</p>
  </div>
  <div class="feature" style="left:210px">
    <div class="icon">
      <svg width="56" height="40" viewBox="0 0 56 40" fill="none" stroke="#222" stroke-width="3" stroke-linejoin="round" stroke-linecap="round">
        <path d="M3 10 L12 8 L16 24 L8 26 Z" fill="#222"/>
        <path d="M53 10 L44 8 L40 24 L48 26 Z" fill="#222"/>
        <path d="M15 12 L24 10 L32 14"/>
        <path d="M41 12 L32 10 L22 17 C20 19 23 21 25 19 L30 16"/>
        <path d="M16 23 L27 32 C29 33 31 31 29 29"/>
        <path d="M22 26 L30 32 C32 33 34 31 32 29"/>
        <path d="M27 24 L34 29 C36 30 37 28 35 26"/>
        <path d="M30 16 L40 23"/>
      </svg>
    </div>
    <div><h3>Our Values</h3><p>Artis nisi ut aliquip ex ea commodoll eros et accumsan o dignss qui nulla facilisi..[+]</p></div>
  </div>
  <div class="feature" style="left:693px">
    <div class="icon"><svg width="50" height="44" viewBox="0 0 50 44"><path d="M25 2 L48 14 H2 Z" fill="#222"/><rect x="6" y="17" width="6" height="18" fill="#222"/><rect x="17" y="17" width="6" height="18" fill="#222"/><rect x="28" y="17" width="6" height="18" fill="#222"/><rect x="39" y="17" width="6" height="18" fill="#222"/><rect x="2" y="37" width="46" height="5" fill="#222"/></svg></div>
    <div><h3>Our Firm</h3><p>Artis nisi ut aliquip ex ea commodoll eros et accumsan o dignss qui nulla facilisi..[+]</p></div>
  </div>
</section>

<section class="abs practice">
  <h2 class="section-title">Practice <u>Areas</u></h2>

  <div class="tile hover" style="left:82px;top:122px">
    <div class="photo" role="img" aria-label="Hands in handcuffs" style="background:linear-gradient(160deg,#9fb0bd,#5f7485)"></div>
    <div class="shade"></div>
    <div class="label">Crimimal</div>
    <div class="blurb">Lorem ipsum dolor sit amet, consectetuer adipiscing elit, sed diam nonummy nibh euismod</div>
    <svg class="plus" width="38" height="38" viewBox="0 0 38 38"><circle cx="19" cy="19" r="17" fill="none" stroke="#fff" stroke-width="2"/><path d="M19 11 V27 M11 19 H27" stroke="#fff" stroke-width="2"/></svg>
  </div>
  <div class="tile" style="left:437px;top:122px">
    <div class="photo" role="img" aria-label="Family standing in front of their house" style="background:linear-gradient(170deg,#dfe4e8,#9aa3a8)"></div>
    <div class="shade"></div><div class="label">Citizenship &amp;<br>Residence</div>
  </div>
  <div class="tile" style="left:793px;top:122px">
    <div class="photo" role="img" aria-label="Advisers shaking hands with a client" style="background:linear-gradient(170deg,#e8e6e1,#a9a59c)"></div>
    <div class="shade"></div><div class="label">Sovereign Patron<br>Pathway</div>
  </div>

  <div class="tile" style="left:82px;top:504px">
    <div class="photo" role="img" aria-label="Judge's gavel on a desk" style="background:linear-gradient(170deg,#6b7887,#3d4755)"></div>
    <div class="shade"></div><div class="label">Criminal Defence</div>
  </div>
  <div class="tile" style="left:437px;top:504px">
    <div class="photo" role="img" aria-label="Worker holding a yellow hard hat" style="background:linear-gradient(170deg,#c9cbc9,#e2b733 45%,#6d7377)"></div>
    <div class="shade"></div><div class="label">Civil Litigation</div>
  </div>
  <div class="tile" style="left:793px;top:504px">
    <div class="photo" role="img" aria-label="Press microphones held out" style="background:linear-gradient(170deg,#e8ecef,#8e979d)"></div>
    <div class="shade"></div><div class="label" style="bottom:auto;top:190px">Media Law</div>
  </div>

  <div class="tile" style="left:82px;top:887px">
    <div class="photo" role="img" aria-label="Businessmen talking in an office" style="background:linear-gradient(170deg,#9fb3c3,#4a5a68)"></div>
    <div class="shade"></div><div class="label">Arbitration<br>and ADR</div>
  </div>
  <div class="tile" style="left:437px;top:887px">
    <div class="photo" role="img" aria-label="Hand signing a document before office towers" style="background:linear-gradient(170deg,#2f5f9c,#8fb4d4 60%,#c9d6e0)"></div>
    <div class="shade"></div><div class="label">Commercial and<br>Corporate</div>
  </div>
  <div class="tile" style="left:793px;top:887px">
    <div class="photo" role="img" aria-label="Hands in handcuffs" style="background:linear-gradient(170deg,#8a969f,#4e5a64)"></div>
    <div class="shade"></div><div class="label" style="bottom:auto;top:190px">Crimimal</div>
  </div>
</section>

<section class="abs cases">
  <h2 class="section-title">Case <u>Studies</u></h2>
  <article class="case" style="left:82px">
    <div class="frame"><div class="photo" role="img" aria-label="Shelves of leather-bound law books" style="background:linear-gradient(180deg,#6b4a2c,#a57b3e,#3b2818)"></div>
      <div class="date"><span class="d">06</span><span class="m">Jun</span></div></div>
    <h4>Lorem Ipsum Dolor Sit Amet Consectetur</h4>
    <p>Lorem ipsum dolor sit amet, consectetur adipiscing elit. Sed vitae magna tellus. Aenean ante nunc, semper nec cursus non, rutrum ac eros.</p>
    <span class="more">Read More ›</span>
  </article>
  <article class="case" style="left:436px">
    <div class="frame"><div class="photo" role="img" aria-label="Courtroom bench with hands in cuffs" style="background:linear-gradient(180deg,#4a3526,#7a5a44,#2a1f18)"></div>
      <div class="date"><span class="d">06</span><span class="m">Jun</span></div></div>
    <h4>Lorem Ipsum Dolor Sit Amet Consectetur</h4>
    <p>Lorem ipsum dolor sit amet, consectetur adipiscing elit. Sed vitae magna tellus. Aenean ante nunc, semper nec cursus non, rutrum ac eros.</p>
    <span class="more">Read More ›</span>
  </article>
  <article class="case" style="left:790px">
    <div class="frame"><div class="photo" role="img" aria-label="Person signing papers at a desk" style="background:linear-gradient(180deg,#3a3430,#bfb8ae,#efece6)"></div>
      <div class="date"><span class="d">07</span><span class="m">Jun</span></div></div>
    <h4>Lorem Ipsum Dolor Sit Amet Consectetur</h4>
    <p>Lorem ipsum dolor sit amet, consectetur adipiscing elit. Sed vitae magna tellus. Aenean ante nunc, semper nec cursus non, rutrum ac eros.</p>
    <span class="more">Read More ›</span>
  </article>
</section>
<div class="view-all"><span>VIEW ALL</span><b><svg width="10" height="14"><path d="M2 2 L8 7 L2 12" stroke="#fff" stroke-width="2" fill="none"/></svg></b></div>

<section class="abs testimonials">
  <h2 class="section-title">Client <u>Testimonials</u></h2>
  <div class="t-arrow" style="left:30px;background:#ccc"><svg width="10" height="14"><path d="M8 2 L2 7 L8 12" stroke="#fff" stroke-width="2" fill="none"/></svg></div>
  <div class="t-arrow" style="right:30px;background:#333"><svg width="10" height="14"><path d="M2 2 L8 7 L2 12" stroke="#fff" stroke-width="2" fill="none"/></svg></div>
  <div class="quote" style="left:96px">
    <div class="who"><div class="avatar" role="img" aria-label="Client portrait"></div><div class="name">- Mark Vella</div></div>
    <p>“ Lorem ipsum sit amet co adipiscitsedulml eiusmo dtepor incidunt ut la dolore ma aliquaenl kni enim nim veni exercitation ullamco ips sdlitnol ameti co adipiscig elitsed do eiusmod te epo uen Accusant dol oremque laudantium. ”</p>
  </div>
  <div class="quote" style="left:672px">
    <div class="who"><div class="avatar" role="img" aria-label="Client portrait"></div><div class="name">- Anna Grech</div></div>
    <p>“ Lorem ipsum sit amet co adipiscitsedulml eiusmo dtepor incidunt ut la dolore ma aliquaenl kni enim nim veni exercitation ullamco ips sdlitnol ameti co adipiscig elitsed do eiusmod te epo uen Accusant dol oremque laudantium. ”</p>
  </div>
</section>
<div class="divider"></div>

<footer class="abs footer">
  <div class="links"><h5>QUICK LINKS</h5>
    <ul><li>Home</li><li>About Malta</li><li>Practice Areas</li><li>Case Studies</li><li>Contact Us</li></ul>
  </div>
  <div class="contact"><h5>CONTACT DETAILS</h5>
    <div class="row"><svg width="12" height="16" viewBox="0 0 12 16"><path d="M6 1 C2.5 1 1 3.5 1 6 C1 9.5 6 15 6 15 C6 15 11 9.5 11 6 C11 3.5 9.5 1 6 1 Z" fill="#2f8fd0"/><circle cx="6" cy="6" r="2" fill="#1d1d1d"/></svg>
      <span><b>Galea &amp; Spiteri Advocates</b><br>12/4, Harbour Lane, Valletta<br>88, Olive Grove Street, Mosta</span></div>
    <div class="row"><svg width="14" height="14" viewBox="0 0 14 14"><path d="M3 1 L5 1 L6 4 L4.5 5.5 C5.5 7.5 6.5 8.5 8.5 9.5 L10 8 L13 9 L13 11 C13 12 12 13 11 13 C5.5 13 1 8.5 1 3 C1 2 2 1 3 1 Z" fill="#2f8fd0"/></svg><b>555-014-229</b></div>
    <div class="row"><svg width="14" height="14" viewBox="0 0 14 14"><rect x="1" y="4" width="12" height="9" fill="#2f8fd0"/><rect x="4" y="1" width="6" height="4" fill="#2f8fd0"/></svg><b>555-014-229</b></div>
    <div class="row"><svg width="14" height="12" viewBox="0 0 14 12"><rect x="1" y="1" width="12" height="10" fill="#2f8fd0"/><path d="M1 1 L7 6 L13 1" stroke="#1d1d1d" fill="none"/></svg>info@galeaspiteri.example</div>
  </div>
  <div class="map" role="img" aria-label="Street map showing the office location"></div>
  <div class="wordmark">Galea &amp; Spiteri</div>
  <div class="f-social"><span></span><span></span><span></span><span></span></div>
  <div class="legal"><span>Terms &amp; Conditions</span><span>Privacy Policy</span></div>
</footer>

<div class="abs copyright">Copyright © 2014 <b>Galea &amp; Spiteri Advocates.</b> All Rights Reserved.</div>

</body>
</html>
```